High-end Oceanfront Real Estate Group Needs Clean, Modern Web Design

I’m looking for a clean, professional, modern and beautiful homepage web design for a Real Estate group in Southern California, USA.

The group/company is “Marwick on the Shore,” and they specialize in high end (i.e. expensive), oceanfront real estate in the Orange County area.

The look and feel of the page should accentuate the brand qualities: luxurious/expensive, professional, and beautiful (Orange County is one of the most beautiful areas in all the US and we would love the site to emphasize the beautiful beaches and scenery it has to offer).

Looks we like:
• www.brantleyhomesrealty.example
• www.closedbyvane.example -- I think the design is pretty out-dated in this site, but I like the organization/layout of the site

Header Tags (I don’t know if we can fit all of these, may need a side-menu, but I’d prefer header title only if possible):
• Welcome
• Featured Listings
• Previously Sold
• Sell
• Property Search
• Team
• Videos
• Blog
• Explore O.C.
• Contact

I have attached the beach and logo pics that we would like to use as the header, a few pictures of the team, and one sample home/view pic which can be used in any of the other sections (for pictures of the homes, just find expensive oceanfront houses and that will be fine).

I promise to provide feedback to each and every design submission. I appreciate the hard work that all of you are putting into your designs. There can be only one contest winner, but I hope to give all of you helpful feedback to submit the best designs possible!

Target Market(s)

Very wealthy home owners of oceanfront properties. These properties are worth several millions of dollars, and thus the site and brand needs to be targeted to very wealthy, successful individuals and families (both US and international buyers).

Industry/Entity Type

Real Estate

Number of Pages Required

2 page

Requirements
Must have
• I don’t want to give too many requirements, because I want to let you all be creative. However, here are the few Must Haves:
• Must submit 2 page designs (a home page and a sub page)
• Must use logo provided
• Focus is mostly on homes, but I would like to include some beach/ocean imagery as well
• The first “item” on the home page should be an accordion/slider which shows pictures of homes and with 1 line of text: “List with the Leader” and two link buttons: “Sell Your Home” and “Buy Your Home”
• Color palette needs to be mainly blues--to match ocean and sky blue
• Exported in all major formats (psd,ai,eps,png,jpeg,etc)
Nice to have
• We don’t necessarily need all of these, but would like to feature most:
• List of videos
• “Meet the Team”—brief team bios and pics
• Link(s) to Blog
• “List with the Leader” – section on why they should choose this firm
• Featured Listings
• Previously Sold

```html
<!DOCTYPE html>
<html lang="en">
<head>
<meta charset="utf-8">
<title>Marwick on the Shore — Oceanfront Real Estate</title>
<link href="https://fonts.googleapis.com/css2?family=Oswald:wght@400;500&family=Open+Sans:wght@400;600;700&display=swap" rel="stylesheet">
<style>
:root{
  --blue:#1f74dc;
  --blue-bright:#2e86ee;
  --blue-deep:#0f4fa8;
  --brand:#4f77a3;
  --ink:#222;
  --muted:#666;
  --panel:#ececec;
  --white:#fff;
  --black:#0d0d0d;
  --dark-tile:#2b2b2b;
}
*{box-sizing:border-box;margin:0;padding:0}
html,body{width:1200px;height:3666px;overflow:hidden}
body{position:relative;font-family:"Open Sans",Arial,sans-serif;color:var(--ink);background:var(--white)}
.abs{position:absolute}
section{position:absolute;left:0;width:1200px;overflow:hidden}

/* hero */
.hero{top:0;height:611px}
.hero-photo{position:absolute;inset:0;background:
  radial-gradient(ellipse 70% 18% at 50% 52%,rgba(255,255,255,.75),rgba(255,255,255,0) 70%),
  linear-gradient(180deg,#2a5a88 0%,#3f72a0 26%,#6f9bc0 42%,#d9e6ee 54%,#b9b3a2 66%,#a38c6c 82%,#8a7558 100%)}
.brand-bar{position:absolute;left:110px;top:0;width:958px;height:171px;background:rgba(255,255,255,.72)}
.brand{position:absolute;left:110px;top:0;width:310px;height:171px;border-right:1px solid rgba(90,127,166,.5);display:flex;align-items:center;gap:10px;padding-left:20px;font-family:"Open Sans",sans-serif;font-weight:600;font-size:24px;color:var(--brand);white-space:nowrap}
.brand .mark{width:14px;height:14px;background:var(--brand);flex:none}
.nav{position:absolute;left:432px;top:116px;display:flex;font-family:"Oswald",sans-serif;font-size:14px;color:var(--blue);letter-spacing:.3px}
.nav span{padding:0 11px;border-right:1px solid var(--blue);line-height:14px}
.nav span:last-child{border-right:0}
.nav-rule{position:absolute;left:420px;top:90px;width:648px;height:1px;background:rgba(90,127,166,.5)}
.social-top{position:absolute;left:822px;top:22px;display:flex;gap:6px}
.social-top i{width:24px;height:24px;border-radius:50%;border:1px solid var(--blue);display:block}
.lang{position:absolute;left:976px;top:22px;width:80px;height:24px;border:1px solid var(--blue);border-radius:12px;font-size:11px;color:var(--blue);padding:4px 10px}
.hero-title{position:absolute;top:304px;width:100%;text-align:center;font-family:"Oswald",sans-serif;font-weight:500;font-size:44px;color:#fff;letter-spacing:1px;text-shadow:0 2px 6px rgba(0,0,0,.45)}
.cta{position:absolute;top:372px;width:313px;height:63px;background:var(--blue-bright);color:#fff;font-family:"Oswald",sans-serif;font-size:30px;display:flex;align-items:center;justify-content:center;gap:18px;border-radius:3px;box-shadow:0 2px 6px rgba(0,0,0,.3)}
.cta svg{width:30px;height:30px}
.thumbs{position:absolute;top:494px;left:0;width:100%;height:95px}
.thumb{position:absolute;top:0;width:170px;height:95px;border:4px solid #fff;box-shadow:0 1px 4px rgba(0,0,0,.35)}
.arrow{position:absolute;top:528px;width:20px;height:28px}

/* search */
.search{top:611px;height:154px;background:#f6f6f6}
.search h2{position:absolute;left:130px;top:14px;font-size:22px;font-weight:700;color:var(--blue)}
.field{position:absolute;height:32px;border:1px solid #ccc;background:#fff;font-size:12px;color:#555;padding:7px 10px}
.field.sel::after{content:"";position:absolute;right:10px;top:9px;width:7px;height:7px;border-right:1.5px solid #333;border-bottom:1.5px solid #333;transform:rotate(45deg)}
.to{position:absolute;left:382px;top:726px;font-size:12px;font-weight:700}
.search-btn{position:absolute;left:940px;top:717px;width:128px;height:32px;background:var(--blue);color:#fff;font-size:12px;display:flex;align-items:center;justify-content:center;gap:8px}

/* welcome */
.welcome{top:765px;height:269px;background:linear-gradient(160deg,#0f63c6 0%,#2a82e3 45%,#0c4fa6 100%);color:#fff;text-align:center}
.welcome h2{margin-top:30px;font-family:"Oswald",sans-serif;font-weight:400;font-size:38px;letter-spacing:1px}
.welcome .rule{width:440px;height:1px;background:rgba(255,255,255,.7);margin:8px auto 12px}
.welcome .sub{font-size:14px;font-weight:700;letter-spacing:5px}
.welcome p{width:940px;margin:14px auto 0;font-size:13px;line-height:22px}

/* section titles */
.sec-title{position:absolute;width:100%;text-align:center;font-size:24px;font-weight:400;color:var(--ink)}
.sec-title::before,.sec-title::after{content:"";display:inline-block;width:170px;height:1px;background:#bbb;vertical-align:middle;margin:0 16px}

/* featured */
.featured{top:1034px;height:376px;background:var(--panel)}
.listing{position:absolute;top:80px;width:274px;height:255px;background:#fff;box-shadow:0 1px 3px rgba(0,0,0,.15)}
.listing .icons{position:absolute;left:0;top:0;width:44px;height:176px;background:var(--dark-tile)}
.listing .icons i{display:block;height:44px;border-bottom:1px solid #444}
.listing .icons i:first-child{background:var(--blue)}
.listing .photo{position:absolute;left:44px;top:0;width:230px;height:146px}
.price-bar{position:absolute;left:44px;top:146px;width:230px;height:30px;background:var(--blue);color:#fff;font-size:14px;font-weight:700;display:flex;align-items:center;gap:8px;padding-left:10px}
.price-bar .dot,.price .dot{width:16px;height:16px;border-radius:50%;border:2px solid currentColor;display:inline-block}
.listing .text{position:absolute;left:54px;top:184px;width:212px;font-size:11px;color:#555;line-height:15px}
.listing .num{position:absolute;left:54px;top:225px;font-size:13px;font-weight:700;color:#555}

/* explore */
.explore{top:1410px;height:428px;background:
  radial-gradient(ellipse 40% 50% at 75% 55%,rgba(120,150,190,.35),rgba(0,0,0,0) 70%),
  linear-gradient(180deg,#0b2a55 0%,#1a4f92 55%,#123f7c 100%);color:#fff;text-align:center}
.explore h2{margin-top:36px;font-size:30px;font-weight:700;letter-spacing:1px}
.explore p{width:940px;margin:16px auto 0;font-size:13px;line-height:19px}
.explore-btn{position:absolute;left:540px;top:186px;width:162px;height:42px;border-radius:21px;background:var(--blue);border:2px solid #fff;font-size:14px;font-weight:700;display:flex;align-items:center;justify-content:center}
.spot{position:absolute;top:270px;width:108px;text-align:center}
.spot .tile{width:86px;height:84px;margin:0 auto;background:#fff;border:3px solid var(--blue)}
.spot .tile i{display:block;width:46px;height:46px;margin:16px auto;background:var(--blue);border-radius:6px}
.spot span{display:block;margin-top:10px;font-size:12px;font-weight:700;line-height:15px}

/* sold */
.sold{top:1838px;height:398px;background:var(--panel)}
.sold .big{position:absolute;left:134px;top:24px;width:404px;height:338px;border:5px solid #fff;box-shadow:0 1px 3px rgba(0,0,0,.2)}
.sold h3{position:absolute;left:567px;top:26px;font-size:18px;font-weight:700;color:var(--blue)}
.sold .line{position:absolute;left:567px;top:56px;width:500px;height:1px;background:#ccc}
.sold .pager{position:absolute;left:1032px;top:26px;display:flex;gap:8px}
.sold p{position:absolute;left:567px;top:66px;width:500px;font-size:13px;line-height:21px;color:#444}
.mini{position:absolute;top:176px;width:153px;height:186px;background:#fff;box-shadow:0 1px 3px rgba(0,0,0,.15)}
.mini .photo{height:124px;border:4px solid #fff}
.mini b{display:block;font-size:12px;padding:6px 8px 0}
.price{display:flex;align-items:center;gap:6px;font-size:12px;font-weight:700;color:var(--blue);padding:5px 8px}

/* team */
.team{top:2236px;height:262px;background:linear-gradient(180deg,#3a8af0 0%,#2a7be0 100%)}
.skyline{position:absolute;left:0;bottom:0;width:1200px;height:140px;background:rgba(20,80,170,.18)}
.avatar{position:absolute;top:60px;width:112px;height:112px;border-radius:50%;border:5px solid #fff;background:linear-gradient(180deg,#b8c8d8,#6b84a0)}
.bubble{position:absolute;top:54px;width:300px;height:140px;background:rgba(15,82,180,.55);border:2px solid rgba(255,255,255,.8);border-radius:6px;color:#fff;font-size:13px;line-height:19px;padding:10px 14px}
.bubble b{display:block;margin-top:10px;font-size:13px}

/* blog */
.blog{top:2498px;height:508px;background:#fff}
.blog-title{position:absolute;width:100%;top:26px;text-align:center;font-size:24px;font-weight:700}
.blog-title::after{content:"";display:block;width:70px;height:2px;background:var(--blue);margin:8px auto 0}
.post{position:absolute;top:117px;width:284px}
.post .side{position:absolute;left:0;top:0;width:48px;height:183px;background:var(--dark-tile)}
.post .date{height:67px;background:var(--blue);color:#fff;text-align:center;font-weight:700;font-size:14px;line-height:20px;padding-top:10px}
.post .date strong{font-size:22px}
.post .side i{display:block;height:58px;border-top:1px solid #444}
.post .photo{position:absolute;left:48px;top:0;width:236px;height:183px}
.post .body{position:absolute;left:56px;top:196px;width:228px}
.post h4{font-size:14px;font-weight:700}
.post .meta{font-size:9px;color:#777;margin:4px 0}
.post p{font-size:11px;color:#555;line-height:15px}
.read{display:inline-block;margin-top:10px;width:96px;height:30px;border-radius:15px;background:var(--blue);color:#fff;font-size:11px;font-weight:700;text-align:center;line-height:30px}

/* consult */
.consult{top:3006px;height:342px;background:#dfe6ee}
.consult-photo{position:absolute;left:560px;top:0;width:640px;height:342px;background:linear-gradient(90deg,#cfd9e4,#eef2f6 60%,#d6dde6)}
.consult h3{position:absolute;right:708px;top:80px;font-weight:700;font-size:21px;color:#fff;text-align:right}
.consult h3 span{font-weight:400}
.consult .lead{position:absolute;right:708px;top:122px;width:360px;font-size:14px;line-height:22px;color:#fff;text-align:right}
.envelope{position:absolute;left:516px;top:107px;width:106px;height:106px;border-radius:50%;background:#e9e9e9;border:4px solid #fff;display:flex;align-items:center;justify-content:center}
.input{position:absolute;left:684px;width:300px;height:36px;background:rgba(255,255,255,.25);border:1px solid rgba(255,255,255,.85);color:#fff;font-size:13px;padding:8px 10px}
.send{position:absolute;left:684px;top:250px;width:92px;height:34px;background:var(--blue);color:#fff;font-size:14px;font-weight:700;text-align:center;line-height:34px}

/* footer */
.footer{top:3348px;height:257px;background:var(--black);color:#fff}
.footer h5{position:absolute;top:34px;font-size:14px;font-weight:700}
.links{position:absolute;top:72px;font-size:12px;line-height:25px;color:#ddd}
.links div::before{content:"› ";color:#aaa}
.follow{position:absolute;left:134px;top:194px;display:flex;align-items:center;gap:8px;font-size:13px;font-weight:700}
.follow i{width:24px;height:24px;border-radius:50%;background:#444;display:block}
.video-tab{position:absolute;left:440px;top:-12px;width:316px;height:269px;background:#1a1a1a}
.video{position:absolute;left:466px;top:76px;width:266px;height:146px;border:3px solid #fff;background:linear-gradient(180deg,#5f7893,#c9d1d8 60%,#3b3b3b)}
.video .play{position:absolute;left:108px;top:48px;width:50px;height:36px;background:#111;border-radius:6px}
.video .play::after{content:"";position:absolute;left:20px;top:10px;border-left:14px solid #fff;border-top:8px solid transparent;border-bottom:8px solid transparent}
.newsletter{position:absolute;left:815px;top:70px;width:252px;height:140px;background:#1c1c1c;padding:12px;font-size:12px;line-height:17px;color:#ddd}
.email{position:absolute;left:12px;top:92px;width:180px;height:32px;background:#fff;color:#777;font-size:12px;padding:7px 10px}
.go{position:absolute;left:198px;top:92px;width:40px;height:32px;background:var(--blue);color:#fff;font-weight:700;font-size:13px;text-align:center;line-height:32px}
.copyright{top:3605px;height:61px;background:#1b1b1b;color:#eee;font-size:12px;font-weight:700;text-align:center;line-height:61px}
</style>
</head>
<body>

<section class="hero">
  <div class="hero-photo" role="img" aria-label="Orange County beach with surf rolling onto the sand"></div>
  <div class="brand-bar"></div>
  <div class="brand"><span class="mark"></span>Marwick on the Shore</div>
  <div class="nav-rule"></div>
  <div class="social-top"><i></i><i></i><i></i><i></i></div>
  <div class="lang">English ▾</div>
  <nav class="nav"><span>HOME</span><span>PROPERTY SEARCH</span><span>TEAM</span><span>VIDEOS</span><span>BLOG</span><span>EXPLORE O.C</span><span>CONTACT</span></nav>
  <h1 class="hero-title">LOOKING FOR A LUXURIOUS &amp; BEAUTIFUL HOME</h1>
  <a class="cta" style="left:244px">SELL YOUR HOME
    <svg viewBox="0 0 30 30"><circle cx="15" cy="15" r="13" fill="none" stroke="#fff" stroke-width="2"/><path d="M12 9l6 6-6 6" fill="none" stroke="#fff" stroke-width="2.5"/></svg></a>
  <a class="cta" style="left:599px">BUY YOUR HOME
    <svg viewBox="0 0 30 30"><circle cx="15" cy="15" r="13" fill="none" stroke="#fff" stroke-width="2"/><path d="M12 9l6 6-6 6" fill="none" stroke="#fff" stroke-width="2.5"/></svg></a>
  <svg class="arrow" style="left:110px" viewBox="0 0 20 28"><path d="M15 3L5 14l10 11" fill="none" stroke="#fff" stroke-width="4"/></svg>
  <div class="thumbs">
    <div class="thumb" style="left:147px;background:linear-gradient(#6aa3d8,#3d6b45)" role="img" aria-label="Palm trees beside a luxury villa"></div>
    <div class="thumb" style="left:332px;background:linear-gradient(#7fb3e2,#4c6b3a)" role="img" aria-label="Tropical garden home"></div>
    <div class="thumb" style="left:516px;background:linear-gradient(#24375a,#9a7b55)" role="img" aria-label="Modern mansion at dusk"></div>
    <div class="thumb" style="left:700px;background:linear-gradient(#3a3a4a,#b28a5a)" role="img" aria-label="Lit house exterior at night"></div>
    <div class="thumb" style="left:884px;background:linear-gradient(#4a8fd8,#c9a27a)" role="img" aria-label="Contemporary home with pool"></div>
  </div>
  <svg class="arrow" style="left:1066px" viewBox="0 0 20 28"><path d="M5 3l10 11L5 25" fill="none" stroke="#fff" stroke-width="4"/></svg>
</section>

<section class="search">
  <h2>Search Commercial REAL ESTATE LISTINGS</h2>
</section>
<div class="field sel abs" style="left:130px;top:668px;width:400px">Property Type</div>
<div class="field abs" style="left:555px;top:668px;width:370px">Type Location or Project or Keyword</div>
<div class="field sel abs" style="left:130px;top:717px;width:225px">Min Price</div>
<div class="to">To</div>
<div class="field sel abs" style="left:412px;top:717px;width:228px">Mix Price</div>
<div class="field sel abs" style="left:660px;top:717px;width:260px">Posted by- All</div>
<div class="search-btn">Search
  <svg width="14" height="14" viewBox="0 0 14 14"><circle cx="6" cy="6" r="4.5" fill="none" stroke="#fff" stroke-width="2"/><path d="M9.5 9.5L13 13" stroke="#fff" stroke-width="2"/></svg></div>

<section class="welcome">
  <h2>WELCOME TO MARWICK</h2>
  <div class="rule"></div>
  <div class="sub">ON THE SHORE</div>
  <p>Lorem ipsum dolor sit amet, consectetuer adipiscing elit, sed diam nonummy nibh euismod tincidunt ut laoreet dolore magna aliquam erat volutpat. Ut wisi enim ad minim veniam, quis nostrud exerci tation ullamcorper suscipit lobortis nisl ut aliquip ex ea commodo consequat. Duis autem vel eum iriure dolor in hendrerit in vulputate velit esse molestie consequat, vel illum dolore eu feugiat nulla facilisis at vero eros et accumsan et iusto odio dignissim qui blandit praesent luptatum zzril delenit augue duis dolore te feugait nulla facilisi.</p>
</section>

<section class="featured">
  <h2 class="sec-title" style="top:24px">Featured Listings</h2>
  <div class="listing" style="left:134px">
    <div class="icons"><i></i><i></i><i></i><i></i></div>
    <div class="photo" style="background:linear-gradient(#6ea9e0,#3f6d48 60%,#3aa0c8)" role="img" aria-label="Villa with palms and pool"></div>
    <div class="price-bar"><span class="dot"></span>23,000,000</div>
    <div class="text">Lorem ipsum dolor sit amet, consectetuer adipiscing elit, sed diam</div>
    <div class="num">Listing # 15880273</div>
  </div>
  <div class="listing" style="left:459px">
    <div class="icons"><i></i><i></i><i></i><i></i></div>
    <div class="photo" style="background:linear-gradient(#7db6e6,#5a7a4a 55%,#c8b08a)" role="img" aria-label="Oceanfront house with palm trees"></div>
    <div class="price-bar"><span class="dot"></span>23,000,000</div>
    <div class="text">Lorem ipsum dolor sit amet, consectetuer adipiscing elit, sed diam</div>
    <div class="num">Listing # 15880273</div>
  </div>
  <div class="listing" style="left:792px">
    <div class="icons"><i></i><i></i><i></i><i></i></div>
    <div class="photo" style="background:linear-gradient(#1f3e6e,#b88a58 60%,#3aa0c8)" role="img" aria-label="Modern home lit at dusk with pool"></div>
    <div class="price-bar"><span class="dot"></span>23,000,000</div>
    <div class="text">Lorem ipsum dolor sit amet, consectetuer adipiscing elit, sed diam</div>
    <div class="num">Listing # 15880273</div>
  </div>
</section>

<section class="explore" role="img" aria-label="Tree-lined evening view of an Orange County home">
  <h2>EXPLORE ORANGE COUNTY</h2>
  <p>Lorem ipsum dolor sit amet, consectetur adipiscing elit. Proin sollicitudin, odio ac molestie blandit, diam elit consequat ligula, in rhoncus diam risus tincidunt orci. Pellentesque vitae massa euismod, pulvinar nunc non, egestas felis. Integer vulputate, erat nec congue porta, arcu risus pulvinar lacus, quis interdum sem risus sed ut. Donec tempus neque vel ligula.</p>
  <div class="explore-btn">EXPLORE MORE</div>
  <div class="spot" style="left:181px"><div class="tile"><i></i></div><span>Harbor Berry Farm</span></div>
  <div class="spot" style="left:331px"><div class="tile"><i></i></div><span>Lantern Kingdom Park</span></div>
  <div class="spot" style="left:481px"><div class="tile"><i></i></div><span>Seabright Ballpark</span></div>
  <div class="spot" style="left:631px"><div class="tile"><i></i></div><span>Coral Bluff State Park</span></div>
  <div class="spot" style="left:782px"><div class="tile"><i></i></div><span>Canyon Grove Zoo</span></div>
  <div class="spot" style="left:931px"><div class="tile"><i></i></div><span>Pacific Surf Heritage Museum</span></div>
</section>

<section class="sold">
  <div class="big" style="background:linear-gradient(#7fb1e0,#a07a52 55%,#2d8fd0)" role="img" aria-label="Modern timber house with a blue pool"></div>
  <h3>SOLD PROPERTIES</h3>
  <div class="pager">
    <svg width="14" height="16" viewBox="0 0 14 16"><path d="M10 2L4 8l6 6" fill="none" stroke="#1f74dc" stroke-width="3"/></svg>
    <svg width="14" height="16" viewBox="0 0 14 16"><path d="M4 2l6 6-6 6" fill="none" stroke="#1f74dc" stroke-width="3"/></svg>
  </div>
  <div class="line"></div>
  <p>Lorem ipsum dolor sit amet, consectetuer adipiscing elit, sed diam nonummy nibh euismod tincidunt ut laoreet dolore magna aliquam erat volutpat. Ut wisi enim ad minim veniam, quis nostrud exerci tation ullamcorper suscipit lobortis nisl ut aliquip ex ea commodo consequat.</p>
  <div class="mini" style="left:567px"><div class="photo" style="background:linear-gradient(#5c90c8,#2f8ac6)" role="img" aria-label="Pool terrace"></div><b>Lorem ipsum dolor</b><div class="price"><span class="dot"></span>23,000,000</div></div>
  <div class="mini" style="left:741px"><div class="photo" style="background:linear-gradient(#4e6ea8,#c79a6a)" role="img" aria-label="Home at sunset"></div><b>Lorem ipsum dolor</b><div class="price"><span class="dot"></span>23,000,000</div></div>
  <div class="mini" style="left:915px"><div class="photo" style="background:linear-gradient(#34557e,#8a9fb5)" role="img" aria-label="Glass house by the water"></div><b>Lorem ipsum dolor</b><div class="price"><span class="dot"></span>23,000,000</div></div>
</section>

<section class="team">
  <div class="skyline"></div>
  <div class="avatar" style="left:134px" role="img" aria-label="Portrait of agent Theo"></div>
  <div class="bubble" style="left:282px">Lorem ipsum dolor sit amet, consectetur adipiscing elit. Proinsollicitudin, odio ac molestie blandit, diam elit consequat ligula, in rhoncus diam risus tincidunt orci<b>THEO</b></div>
  <div class="avatar" style="left:617px" role="img" aria-label="Portrait of agent Lena Marwick"></div>
  <div class="bubble" style="left:766px">Lorem ipsum dolor sit amet, consectetur adipiscing elit. Proinsollicitudin, odio ac molestie blandit, diam elit consequat ligula, in rhoncus diam risus tincidunt orci<b>LENA MARWICK</b></div>
</section>

<section class="blog">
  <h2 class="blog-title">LATEST FROM BLOG</h2>
  <article class="post" style="left:130px">
    <div class="side"><div class="date">FEB<br><strong>28</strong></div><i></i><i></i></div>
    <div class="photo" style="background:linear-gradient(#d8dde3,#6c7d90)" role="img" aria-label="Bright living room with ocean view"></div>
    <div class="body"><h4>benefits of a reputable cabinet...</h4><div class="meta">MAY 07, 2014 &nbsp;|&nbsp; 4 COMMENTS &nbsp;|&nbsp; ♥ 54</div><p>Lorem ipsum dolor sit amet, consectetuer adipiscing elit, sed diam nonummy nibh euismod tincidunt ut</p><span class="read">Read More</span></div>
  </article>
  <article class="post" style="left:442px">
    <div class="side"><div class="date">FEB<br><strong>26</strong></div><i></i><i></i></div>
    <div class="photo" style="background:linear-gradient(#3a6aa8,#1f3552)" role="img" aria-label="Infinity pool house at twilight"></div>
    <div class="body"><h4>benefits of a reputable cabinet...</h4><div class="meta">MAY 07, 2014 &nbsp;|&nbsp; 4 COMMENTS &nbsp;|&nbsp; ♥ 54</div><p>Lorem ipsum dolor sit amet, consectetuer adipiscing elit, sed diam nonummy nibh euismod tincidunt ut</p><span class="read">Read More</span></div>
  </article>
  <article class="post" style="left:784px">
    <div class="side"><div class="date">FEB<br><strong>25</strong></div><i></i><i></i></div>
    <div class="photo" style="background:linear-gradient(#2e5fa8,#a87a4e)" role="img" aria-label="Terraced hillside home at dusk"></div>
    <div class="body"><h4>benefits of a reputable cabinet...</h4><div class="meta">MAY 07, 2014 &nbsp;|&nbsp; 4 COMMENTS &nbsp;|&nbsp; ♥ 54</div><p>Lorem ipsum dolor sit amet, consectetuer adipiscing elit, sed diam nonummy nibh euismod tincidunt ut</p><span class="read">Read More</span></div>
  </article>
</section>

<section class="consult">
  <div class="consult-photo" role="img" aria-label="Smiling consultant in a bright office"></div>
  <svg class="abs" style="left:0;top:0" width="1200" height="342" viewBox="0 0 1200 342">
    <polygon points="0,0 640,0 520,342 0,342" fill="#2a7fe4"/>
    <polygon points="640,0 1200,0 1200,342 520,342" fill="#2a7fe4" opacity=".35"/>
  </svg>
  <h3>REQUEST <span>A CONSULT</span></h3>
  <div class="lead">GET STARTED BY FILLING OUT OUR ONLINE ENQUIRY FORM, WE'LL GET IN TOUCH WITHIN <b>24 HOURS</b></div>
  <div class="envelope"><svg width="46" height="34" viewBox="0 0 46 34"><rect x="1" y="1" width="44" height="32" rx="3" fill="#8a8a8a"/><path d="M2 3l21 16L44 3" fill="none" stroke="#e9e9e9" stroke-width="3"/></svg></div>
  <div class="input" style="top:18px">Name</div>
  <div class="input" style="top:66px">Email</div>
  <div class="input" style="top:114px">Phone Number</div>
  <div class="input" style="top:162px;height:70px">Your Message</div>
  <div class="send">Send</div>
</section>

<section class="footer" style="overflow:visible">
  <h5 style="left:134px">Quick Links</h5>
  <div class="abs" style="left:134px;top:60px;width:266px;height:1px;background:#333"></div>
  <div class="links" style="left:140px"><div>Home</div><div>About</div><div>Property Search</div><div>Explore O.C</div></div>
  <div class="links" style="left:276px"><div>Team</div><div>Videos</div><div>Blog</div><div>Contact</div></div>
  <div class="follow">Follow Us On <i></i><i></i><i></i><i></i></div>
  <div class="video-tab"></div>
  <h5 style="left:474px">Our Video</h5>
  <div class="video" role="img" aria-label="Video preview of a luxury home interior"><div class="play"></div></div>
  <h5 style="left:815px">Newsletter Signup</h5>
  <div class="newsletter">Lorem ipsum dolor siamet consetuge sed diay nibh euismod tlut ut laoreet dolore magam.
    <div class="email">✉ &nbsp;Email Address</div><div class="go">GO</div></div>
</section>

<section class="copyright">© 2015 Marwick on the Shore. &nbsp;All Rights Reserved.</section>

</body>
</html>
```